Health Wellbeing Beauty online Shop

I have attached a full spec, however in summary this is a new business startup selling skincare products.

We need a web design for new wellbeing website, selling skincare products so need an eCommerce solution . On the home page I would like these faces to dissolve into each other on a loop or use a honeycomb style transation.
You will need the option of being able to log into an account, either through lumigram, vexora, chirplo or create an account. For created accounts, obviously need the facility to be able to reset passwords, see previous orders, track current order, and maintain favourites.
It should be PC, mobile and tablet friendly.

Look and Feel
It should be an elegant, modern, professional, trendy, unisex website. It should look clean and calm. Am happy to try interesting and slightly unusual designs. I would also like to have chat functionality, either powered by talvuNchat or by Quo 58.
Websites I like are
https://www.nobel-radiance.example.co.uk/
https://www.mereminerals.example.co.uk/
http://www.brightdermis.example.com/

PLEASE DO USE YOUR KNOWELDGE OF WHAT WORKS FOR WEB DESIGN. YOU’RE THE EXPERT AND NEED YOUR EXPERTISE. CARTE BLANCHE TO DESIGN AS YOU SEE FIT. Please be creative, I need my site to stand out from the crowd.

Target Market(s)

Target Market
Middle aged women are our most common client, however, younger patients, both male and female, will often visit the site. In summary, I would like the site to appeal to all age brackets.

Industry/Entity Type

Business

Coding

Coded - Design and coding required

Number of Pages Required

4 page

Requirements
Must have
• Need shop to be exactly like shop on this link http://www.brightdermis.example.com/
Nice to have
• i would like something unique and creative

```html
<!DOCTYPE html>
<html lang="en">
<head>
<meta charset="utf-8">
<title>Aurelle Beauty Shop</title>
<link href="https://fonts.googleapis.com/css2?family=Jost:wght@300;400;500&display=swap" rel="stylesheet">
<style>
:root{
  --ink:#2b2b2b;
  --muted:#555;
  --line:#dcdcdc;
  --brown:#8a5a1e;
  --gold:#b98a34;
  --price:#c24d6e;
  --cream:#fdf3e6;
  --hero-bg:#e9e6e2;
  --white:#fff;
  --social:#2f6fb4;
}
*{box-sizing:border-box;margin:0;padding:0}
html,body{width:1200px;height:3072px;overflow:hidden}
body{position:relative;background:var(--white);font-family:"Jost",Arial,sans-serif;color:var(--ink)}
.abs{position:absolute}
a{color:inherit;text-decoration:none}

/* header */
.brand{left:98px;top:30px;width:192px}
.brand-mark{display:flex;align-items:center;justify-content:center;gap:10px;font-size:42px;font-weight:400;letter-spacing:2px;height:60px;line-height:60px}
.brand-mark .dot{width:14px;height:14px;border-radius:50%;background:var(--ink)}
.toplinks{left:686px;top:24px;display:flex;gap:22px;font-size:11.5px;align-items:center}
.toplinks .login{color:var(--gold)}
.toplinks .sep{width:1px;height:16px;background:var(--line)}
.social-mini{display:flex;gap:6px;font-size:10.5px;color:var(--social)}
.search{left:642px;top:72px;width:360px;height:44px;border:1px solid var(--line);display:flex;align-items:center;font-size:12px;padding-left:16px;color:var(--muted)}
.search .btn{position:absolute;right:0;top:0;width:44px;height:42px;border-left:1px solid var(--line);display:flex;align-items:center;justify-content:center}
.basket{left:1028px;top:56px;width:66px;text-align:center;font-size:12px}
.nav{left:98px;top:136px;width:1004px;height:48px;border-top:1px solid var(--line);display:flex;justify-content:space-between;align-items:center;font-size:13px}

/* hero */
.hero{left:0;top:186px;width:1200px;height:492px;background:var(--hero-bg);overflow:hidden}
.hero-photo{position:absolute;right:0;top:0;width:700px;height:492px;background:linear-gradient(90deg,#e9e6e2 0%,#dcc3ad 35%,#c99d80 65%,#b98b6e 100%)}
.hero-title{position:absolute;left:112px;top:90px;font-size:104px;font-weight:300;line-height:98px;text-align:center;width:300px}
.hero-sub{position:absolute;left:90px;top:296px;width:360px;font-size:20px;font-weight:300;color:var(--muted);text-align:center;line-height:30px}
.dots{position:absolute;left:254px;top:438px;display:flex;gap:9px}
.dots span{width:10px;height:10px;border-radius:50%;background:var(--ink)}
.dots span.off{background:transparent;border:1.5px solid var(--ink)}

/* products */
.section-title{width:1200px;left:0;text-align:center;font-size:40px;font-weight:300}
.toolbar{left:98px;top:782px;width:1004px;height:48px;border-bottom:1px solid var(--line);display:flex;align-items:flex-start;font-size:13px}
.select{display:inline-flex;align-items:center;border:1px solid var(--line);height:30px;padding-left:8px;font-size:12px;margin-left:14px;position:relative}
.select .arrow{width:26px;height:28px;background:var(--ink);margin-left:auto;display:flex;align-items:center;justify-content:center}
.pager{display:flex;gap:10px;margin-left:56px;font-size:14px}
.refine{left:98px;top:862px;width:183px;font-size:24px;font-weight:300;padding-bottom:8px;border-bottom:1px solid var(--line)}
.filter-head{left:98px;font-size:11px;font-weight:500;display:flex;gap:6px;align-items:center;width:183px;border-top:1px solid var(--line);padding-top:10px}
.filter-box{left:98px;width:183px;border:1px solid var(--line);font-size:10.5px;padding:8px 24px 8px 10px}
.filter-box .scroll{position:absolute;right:4px;top:4px;bottom:4px;width:8px;background:#d8d8d8;border-radius:2px}
.filter-box ul{list-style:none}
.filter-box li{display:flex;align-items:center;gap:10px;height:29px}
.filter-box .cols{display:grid;grid-template-columns:1fr 1fr}
.chk{width:11px;height:11px;border:1px solid #999;flex:none}
.card{width:227px;height:338px;border:1px solid #ececec;text-align:center}
.card .shot{width:150px;height:150px;margin:22px auto 0;border-radius:4px}
.card h3{font-size:16px;font-weight:400;line-height:22px;margin-top:12px}
.card .price{color:var(--price);font-size:18px;margin-top:6px}
.card .shop{display:inline-block;background:var(--brown);color:var(--white);font-size:17px;width:138px;height:38px;line-height:38px;margin-top:12px}

/* contact */
.contact{left:0;top:1683px;width:1200px;height:580px;background:var(--cream);text-align:center}
.contact h2{position:absolute;left:0;top:36px;width:1200px;font-size:40px;line-height:48px;font-weight:300}
.contact .lead{position:absolute;left:0;top:93px;width:1200px;font-size:17px;line-height:24px;font-weight:300}
.contact .info{position:absolute;left:0;top:128px;width:1200px;font-size:13.5px;line-height:19px}
.contact .info .label{color:var(--gold);font-size:18px;line-height:24px}
.field{position:absolute;height:44px;border:1px solid #cfcfcf;background:var(--white);font-size:12px;color:#888;text-align:left;padding:14px 16px}
.send{position:absolute;left:506px;top:484px;width:186px;height:45px;background:var(--brown);color:var(--white);font-size:16px;line-height:45px;letter-spacing:.5px}

/* about */
.about{left:0;top:2263px;width:1200px;height:410px;background:var(--white);overflow:hidden}
.about-photo{position:absolute;right:0;top:0;width:620px;height:410px;background:linear-gradient(90deg,#ffffff 0%,#f1e6da 30%,#dfc2a6 60%,#c8a082 100%)}
.about h2{position:absolute;left:98px;top:50px;font-size:40px;font-weight:300;color:var(--gold)}
.about p{position:absolute;left:98px;width:584px;font-size:11.5px;line-height:19px;color:var(--ink)}

/* footer */
.footer{left:0;top:2673px;width:1200px;height:399px;background:var(--cream)}
.f-brand{position:absolute;left:98px;top:60px;width:160px}
.f-brand .brand-mark{font-size:32px;height:60px;line-height:60px}
.f-desc{position:absolute;left:98px;top:162px;width:185px;font-size:11.5px;line-height:17px;letter-spacing:.6px}
.f-col{position:absolute;top:56px;font-size:11.5px;letter-spacing:1px}
.f-col h4{font-size:15px;font-weight:400;letter-spacing:2px;margin-bottom:26px}
.f-col li{list-style:none;height:23.3px}
.f-div{position:absolute;top:48px;width:1px;height:270px;background:#e6d8c4}
.f-social{display:flex;gap:8px;margin-top:34px}
.f-social span{width:32px;height:32px;border-radius:50%;background:var(--social)}
.f-social-names{font-size:10px;letter-spacing:.5px;margin-top:8px;color:var(--social)}
.f-bottom{position:absolute;left:98px;top:327px;width:1004px;border-top:1px solid #e6d8c4;display:flex;justify-content:space-between;padding-top:22px;font-size:12px}
</style>
</head>
<body>

<header>
  <div class="abs brand">
    <div class="brand-mark"><span class="dot"></span>Aurelle</div>
  </div>
  <div class="abs toplinks">
    <a class="login" href="#">LOGIN</a>
    <a href="#">CREATE AN ACCOUNT</a>
    <span class="sep"></span>
    <span>CONNECT US</span>
    <span class="social-mini"><span>chirplo</span><span>lumigram</span><span>linkora</span><span>vexora</span></span>
  </div>
  <div class="abs search">SEARCH
    <span class="btn"><svg width="16" height="16" viewBox="0 0 16 16"><circle cx="7" cy="7" r="5" fill="none" stroke="#333" stroke-width="1.8"/><line x1="11" y1="11" x2="15" y2="15" stroke="#333" stroke-width="1.8"/></svg></span>
  </div>
  <div class="abs basket">
    <svg width="52" height="44" viewBox="0 0 52 44">
      <path d="M10 18 Q26 2 42 18" fill="none" stroke="#333" stroke-width="2.5"/>
      <path d="M4 18 H48 L43 40 H9 Z" fill="#444"/>
      <path d="M12 22 V36 M19 22 V36 M26 22 V36 M33 22 V36 M40 22 V36" stroke="#fff" stroke-width="1.5"/>
      <circle cx="44" cy="8" r="8" fill="var(--gold)"/>
      <text x="44" y="12" font-size="11" fill="#fff" text-anchor="middle" font-family="Jost, sans-serif">0</text>
    </svg>
    <div>BASKET</div>
  </div>
  <nav class="abs nav">
    <a href="#">HOME</a><a href="#">SKIN LIGHTENING TABLETS</a><a href="#">SKIN LIGHTENING CREAMS</a><a href="#">SKIN LIGHTENING SOAPS</a><a href="#">SKIN LIGHTENING VIALS</a><a href="#">ABOUT US</a><a href="#">CONTACT</a>
  </nav>
</header>

<section class="abs hero">
  <div class="hero-photo" role="img" aria-label="Close-up of a woman touching her cheek"></div>
  <h1 class="hero-title">Beauty shop</h1>
  <p class="hero-sub">Sunt in culpa qui officia deserunt mollit anim id est laborum</p>
  <div class="dots"><span></span><span class="off"></span><span></span></div>
</section>

<h2 class="abs section-title" style="top:712px">Aurelle Products</h2>

<div class="abs toolbar">
  <span style="margin-top:8px">SHOWING 1 - 12 OF 30</span>
  <span style="margin:8px 0 0 32px">SHOW</span>
  <span class="select" style="width:70px">6<span class="arrow"><svg width="10" height="6"><path d="M0 0 L5 6 L10 0Z" fill="#fff"/></svg></span></span>
  <span style="margin:8px 0 0 auto">SORT BY</span>
  <span class="select" style="width:100px">Name<span class="arrow"><svg width="10" height="6"><path d="M0 0 L5 6 L10 0Z" fill="#fff"/></svg></span></span>
  <span class="pager" style="margin-top:8px"><span>1</span><span>2</span><span>3</span><span>4</span><span>&rsaquo;</span></span>
</div>

<aside>
  <div class="abs refine">REFINE BY</div>
  <div class="abs filter-head" style="top:908px"><svg width="8" height="6"><path d="M0 0 L4 6 L8 0Z" fill="#333"/></svg>CATEGORIES TYPE</div>
  <div class="abs filter-box" style="top:944px;height:162px">
    <span class="scroll"></span>
    <ul><li><span class="chk"></span>Skin Lightening tablets</li><li><span class="chk"></span>Skin Lightening Creams</li><li><span class="chk"></span>Skin Lightening Soaps</li><li><span class="chk"></span>Skin Lightening Vials</li><li><span class="chk"></span>Skin Lightening Systems</li></ul>
  </div>
  <div class="abs filter-head" style="top:1162px"><svg width="8" height="6"><path d="M0 0 L4 6 L8 0Z" fill="#333"/></svg>CATEGORIES COLOUR</div>
  <div class="abs filter-box" style="top:1200px;height:162px">
    <span class="scroll"></span>
    <ul class="cols"><li><span class="chk"></span>Red</li><li><span class="chk"></span>Black</li><li><span class="chk"></span>Blue</li><li><span class="chk"></span>Pink</li><li><span class="chk"></span>Gold</li><li><span class="chk"></span>Green</li><li><span class="chk"></span>Grey</li><li><span class="chk"></span>Orange</li><li><span class="chk"></span>White</li><li><span class="chk"></span>Yellow</li></ul>
  </div>
  <div class="abs filter-head" style="top:1420px"><svg width="8" height="6"><path d="M0 0 L4 6 L8 0Z" fill="#333"/></svg>CATEGORIES SIZE</div>
  <div class="abs filter-box" style="top:1458px;height:160px">
    <span class="scroll"></span>
    <ul><li><span class="chk"></span>W34L26</li><li><span class="chk"></span>W24L26</li><li><span class="chk"></span>W23 L26</li><li><span class="chk"></span>W26 L26</li><li><span class="chk"></span>W28 L26</li></ul>
  </div>
</aside>

<main>
  <article class="abs card" style="left:340px;top:901px"><div class="shot" role="img" aria-label="Set of skincare bottles" style="background:linear-gradient(160deg,#f3e3da,#d9b9a8)"></div><h3>Numquam Eius Modi<br>Tempora Incidunt</h3><div class="price">£39.99</div><a class="shop" href="#">Shop Now !</a></article>
  <article class="abs card" style="left:606px;top:901px"><div class="shot" role="img" aria-label="Silver cream tubes" style="background:linear-gradient(160deg,#f1f1f1,#c9c9c9)"></div><h3>Numquam Eius Modi<br>Tempora Incidunt</h3><div class="price">£39.99</div><a class="shop" href="#">Shop Now !</a></article>
  <article class="abs card" style="left:872px;top:901px"><div class="shot" role="img" aria-label="Pump bottle and jars" style="background:linear-gradient(160deg,#f4ece6,#cdb8a8)"></div><h3>Numquam Eius Modi<br>Tempora Incidunt</h3><div class="price">£39.99</div><a class="shop" href="#">Shop Now !</a></article>
  <article class="abs card" style="left:340px;top:1280px"><div class="shot" role="img" aria-label="Silver serum bottles" style="background:linear-gradient(160deg,#eef0f2,#b8bec4)"></div><h3>Numquam Eius Modi<br>Tempora Incidunt</h3><div class="price">£39.99</div><a class="shop" href="#">Shop Now !</a></article>
  <article class="abs card" style="left:606px;top:1280px"><div class="shot" role="img" aria-label="Blue skincare box and tube" style="background:linear-gradient(160deg,#e4e8ef,#7c8aa3)"></div><h3>Numquam Eius Modi<br>Tempora Incidunt</h3><div class="price">£39.99</div><a class="shop" href="#">Shop Now !</a></article>
  <article class="abs card" style="left:872px;top:1280px"><div class="shot" role="img" aria-label="Skincare collection of tubes and jars" style="background:linear-gradient(160deg,#f2efe9,#c8c2b5)"></div><h3>Numquam Eius Modi<br>Tempora Incidunt</h3><div class="price">£39.99</div><a class="shop" href="#">Shop Now !</a></article>
</main>

<section class="abs contact">
  <h2>Contact Us</h2>
  <p class="lead">Get in touch for expert confidential supplement advice, or for customer services.</p>
  <div class="info">
    <div class="label">Calling from the UK</div>
    <div>0800 123 4567</div>
    <div class="label">Calling from Overseas</div>
    <div>+44 800 123 4567</div>
    <div>To contact us by email, please click the send us a message tab on the right.</div>
    <div class="label">Our team is available</div>
    <div>Monday - Friday: 8am until 18:00pm</div>
    <div>Answerphone out of hours</div>
  </div>
  <div class="field" style="left:100px;top:320px;width:236px">Name</div>
  <div class="field" style="left:354px;top:320px;width:238px">Email</div>
  <div class="field" style="left:608px;top:320px;width:238px">Phone</div>
  <div class="field" style="left:864px;top:320px;width:236px">Service For<svg style="position:absolute;right:16px;top:18px" width="10" height="6"><path d="M0 0 L5 5 L10 0" fill="none" stroke="#777"/></svg></div>
  <div class="field" style="left:100px;top:385px;width:1000px;height:72px">Message</div>
  <a class="send" href="#">SEND A MESSAGE</a>
</section>

<section class="abs about">
  <div class="about-photo" role="img" aria-label="Smiling young woman resting on her arms"></div>
  <h2>About Us</h2>
  <p style="top:108px">Lorem ipsum dolor sit amet, consectetur adipiscing elit. Phasellus non sodales ipsum. Pellentesque ac nisi ex sem suscipit luctus. Duis commodo aliquam mi, non pellentesque est finibus vitae. Maecenas ut faucibus magna, eget volutpat lorem. Nunc vestibulum at nunc ut tincidunt. Curabitur non ante porttitor lectus volutpat imperdiet interdum sit amet erat. Maecenas convallis erat massa, sit amet iaculis purus imperdiet sed. Sed tellus odio, ullamcorper sed elit consectetur, pretium dictum dui.</p>
  <p style="top:226px">Morbi a euismod sapien, ac porttitor sem. Suspendisse molestie ut urna quis accumsan. Suspendisse potenti. Integer id dui elementum, feugiat erat quis, ultrices dolor. Quisque in ullamcorper purus, efficitur ultrices leo. Nullam non gravida nunc, eget interdum mi. Suspendisse ac nisi aliquet, tempus urna vitae, venenatis nibh. Vestibulum aliquet in tellus et aliquet. Praesent consequat arcu et mauris porttitor, ut lacinia dui lobortis. Praesent hendrerit dolor eu faucibus venenatis. Mauris porta auctor ex lacinia mollis. Morbi euismod massa a lacinia porttitor.</p>
</section>

<footer class="abs footer">
  <div class="f-brand">
    <div class="brand-mark"><span class="dot"></span>Aurelle</div>
  </div>
  <p class="f-desc">Middle aged women are our most common client, however, younger patients, both male and female, will often visit the site. In summary, I would like the site to appeal to all age brackets.</p>
  <span class="f-div" style="left:307px"></span>
  <div class="f-col" style="left:328px"><h4>CATEGORIES</h4><ul><li>HOME</li><li>SKIN LIGHTENING TABLETS</li><li>SKIN LIGHTENING CREAMS</li><li>SKIN LIGHTENING SOAPS</li><li>SKIN LIGHTENING VIALS</li><li>ABOUT US</li><li>CONTACT</li></ul></div>
  <span class="f-div" style="left:522px"></span>
  <div class="f-col" style="left:551px"><h4>INFORMATION</h4><ul><li>SPECIALS</li><li>NEW PRODUCTS</li><li>TOP SELLERS</li><li>OUR STORES</li><li>CONTACT US</li><li>ABOUT US</li><li>PAGES CONFIGURATION</li><li>SITEMAP</li></ul></div>
  <span class="f-div" style="left:717px"></span>
  <div class="f-col" style="left:737px"><h4>MY ACCOUNT</h4><ul><li>MY ORDERS</li><li>MY PRODUCTS RETURNS</li><li>MY CREDIT SLIPS</li><li>MY ADDRESSES</li><li>MY PERSONAL INFO</li></ul></div>
  <span class="f-div" style="left:905px"></span>
  <div class="f-col" style="left:932px"><h4>FOLLOW US</h4><div>PLEASE CONNECT WITH US</div>
    <div class="f-social" style="margin-left:14px"><span></span><span></span><span></span><span></span></div>
    <div class="f-social-names" style="margin-left:14px">chirplo · lumigram · linkora · vexora</div>
  </div>
  <div class="f-bottom"><span>© 2016 Company Name &nbsp;All right reserved &nbsp;Term of Use</span><span>C16</span></div>
</footer>

</body>
</html>
```